Graphic background for 10 Pull Up Banners

To produce a graphic background for a 100 cm wide by 200 cm high Pull-Up Display banner containing a Buddhist text in three languages: Tibetan, Mandarin and English. Please refer to uploaded file "Elements of Pull Up Banner". The design should be simple (not drawing attention away from the text). This design should then be varied for or extended to the next banner and so on until the 10th banner. When the banners are lined up, they should form a single design that is 1000 cm wide by 200 cm high.
An alternative way to look at the project is to produce a graphic background of 1000 cm width by 200 cm height that is then splitted into ten separate 100 cm wide by 200 cm high graphic to be used as background for 10 Buddhist texts (text 1, 2, 3, 4, 5, 6, 7, 8, 9a, 9b) on 10 Pull-Up Display Banners, the text in each banner being in the three languages mentioned earlier.
In either perspective, the design should be simple and not draw attention away from the texts. See uploaded PDF file "Examples.pdf"
Target Market(s)
For attendees at a Buddhist Event.
Look and feel
Each slider illustrates characteristics of the customer's brand and the style your logo design should communicate.

```html
<!DOCTYPE html>
<html lang="en">
<head>
<meta charset="utf-8">
<title>Ten Mistaking – Pull-Up Banner</title>
<link rel="stylesheet" href="https://fonts.googleapis.com/css2?family=Nunito:wght@600;700&family=Arimo:wght@400&family=Noto+Sans+SC:wght@400;500&family=Noto+Serif+Tibetan:wght@400&display=swap">
<style>
  :root {
    --page-bg: #eef0f2;
    --maroon: #760606;
    --gold: #f6b428;
    --amber-light: #fdd060;
    --amber: #f9b12c;
    --orange: #f38e14;
    --band-brown: #7c3d09;
    --ink: #2a1a0a;
    --white: #ffffff;
    --panel: rgba(255, 226, 140, 0.38);
  }
  * { box-sizing: border-box; margin: 0; padding: 0; }
  html, body {
    width: 1192px; height: 1200px; overflow: hidden;
    background: var(--page-bg);
  }
  .banner {
    position: absolute; left: 366px; top: 30px;
    width: 460px; height: 1140px; overflow: hidden;
    background:
      radial-gradient(ellipse 160px 90px at 60% 38%, rgba(243,142,20,0.55), transparent 70%),
      radial-gradient(ellipse 140px 120px at 30% 48%, rgba(243,142,20,0.45), transparent 70%),
      radial-gradient(ellipse 220px 80px at 70% 58%, rgba(240,120,10,0.45), transparent 70%),
      radial-gradient(ellipse 180px 120px at 45% 70%, rgba(253,208,96,0.6), transparent 70%),
      linear-gradient(180deg, var(--amber-light) 0%, var(--amber) 30%, var(--orange) 55%, var(--amber) 80%, var(--orange) 100%);
  }
  .logo-box {
    position: absolute; left: 0; top: 15px; width: 156px; height: 222px;
    background: var(--white);
    display: flex; flex-direction: column; align-items: center; justify-content: center; gap: 10px;
  }
  .logo-box .mark {
    width: 44px; height: 44px; border-radius: 50%; background: var(--maroon);
  }
  .logo-box .org-name {
    font: 700 15px/1.2 "Nunito", sans-serif; color: var(--maroon); text-align: center;
  }
  .header-shape { position: absolute; left: 156px; top: 0; }
  .title-zh {
    position: absolute; left: 190px; top: 52px;
    font: 500 34px/1 "Noto Sans SC", sans-serif; color: var(--gold); letter-spacing: 2px;
  }
  .title-en {
    position: absolute; left: 190px; top: 100px;
    font: 600 38px/1 "Nunito", sans-serif; color: var(--gold);
  }
  .text-panel {
    position: absolute; left: 44px; top: 243px; width: 368px; height: 723px;
    background: var(--panel); border-radius: 10px;
  }
  .verses-bo {
    position: absolute; left: 92px; top: 266px;
    font: 400 12px/23.7px "Noto Serif Tibetan", serif; color: var(--ink); list-style: none;
  }
  .verses-zh {
    position: absolute; left: 159px; top: 530px;
    font: 500 11px/14px "Noto Sans SC", sans-serif; color: var(--ink); list-style: none;
  }
  .notes-zh {
    position: absolute; left: 159px; top: 690px;
    font: 500 11px/14px "Noto Sans SC", sans-serif; color: var(--ink); list-style: none;
  }
  .verses-en {
    position: absolute; left: 59px; top: 752px;
    font: 400 7.6px/19.6px "Arimo", sans-serif; color: var(--ink); list-style: none;
  }
  .dedication-band {
    position: absolute; left: 0; top: 1022px; width: 460px; height: 118px;
    background: var(--band-brown); color: var(--white); text-align: center;
  }
  .dedication-band p { position: absolute; left: 0; width: 460px; }
  .dedication-bo { top: 8px; font: 400 12px/1.4 "Noto Serif Tibetan", serif; }
  .dedication-zh { top: 38px; font: 400 11px/1.4 "Noto Sans SC", sans-serif; }
  .dedication-en { top: 64px; font: 400 10px/1.4 "Arimo", sans-serif; }
  .lotus-placeholder {
    position: absolute; left: 345px; top: 28px; width: 64px; height: 52px;
    border-radius: 50% 50% 40% 40%; background: rgba(255,255,255,0.18);
  }
</style>
</head>
<body>
  <main class="banner">
    <div class="logo-box">
      <span class="mark"></span>
      <span class="org-name">Lotus Light<br>Sangha</span>
    </div>

    <svg class="header-shape" width="304" height="226" viewBox="0 0 304 226" aria-hidden="true">
      <path d="M0 0 H304 V166 Q220 170 152 224 Q84 170 0 166 Z" fill="var(--maroon)"/>
    </svg>
    <h1 class="title-zh">十个误解</h1>
    <h2 class="title-en">Ten Mistaking</h2>

    <div class="text-panel"></div>

    <ol class="verses-bo" lang="bo">
      <li>དད་པ་དང་འདོད་པ་ནོར་སྲིད།</li>
      <li>བྱམས་སྙིང་རྗེ་དང་ཆགས་པ་ནོར་སྲིད།</li>
      <li>ཤེས་བྱའི་སྟོང་ཉིད་དང་བློས་བྱས་སྟོང་པ་ནོར་སྲིད།</li>
      <li>ཆོས་ཀྱི་དབྱིངས་དང་ཆད་ལྟ་ནོར་སྲིད།</li>
      <li>ཉམས་མྱོང་དང་རྟོགས་པ་ནོར་སྲིད།</li>
      <li>བརྟུལ་ཞུགས་དང་ཡོན་ཏན་ནོར་སྲིད།</li>
      <li>འཁྲུལ་ཞིག་དང་གདོན་ཞུགས་ནོར་སྲིད།</li>
      <li>གྲུབ་ཐོབ་དང་ཚོད་དཔོན་ནོར་སྲིད།</li>
      <li>གཞན་དོན་དང་རང་དོན་ནོར་སྲིད།</li>
      <li>ཐབས་མཁས་དང་གཡོ་སྒྱུ་ནོར་སྲིད།</li>
    </ol>

    <ol class="verses-zh" lang="zh">
      <li>信心与贪欲可能混淆，</li>
      <li>慈悲与贪爱可能混淆，</li>
      <li>所知¹本空与思维造作空性可能混淆，</li>
      <li>法界与断见²可能混淆，</li>
      <li>觉受与证悟可能混淆，</li>
      <li>尊者与神棍可能混淆，</li>
      <li>破惑与着魔可能混淆，</li>
      <li>成就者与骗子可能混淆，</li>
      <li>利他与自利可能混淆，</li>
      <li>方便善巧与谄媚欺诈可能混淆。</li>
    </ol>
    <ol class="notes-zh" lang="zh">
      <li>1.&nbsp;所知：可以认知的外景。</li>
      <li>2.&nbsp;断见：否定因果、前生、后世等看法的见解。</li>
    </ol>

    <ol class="verses-en">
      <li>Desire can be mistaken for faith or devotion.</li>
      <li>Attachment can be mistaken for love and compassion.</li>
      <li>Conceptual emptiness can be mistaken for the emptiness of the nature of phenomena.</li>
      <li>Nihilism can be mistaken for the dharmadhatu.</li>
      <li>A meditative experience can be mistaken for realization.</li>
      <li>Outer religious practices can be mistaken for inner development of good qualities.</li>
      <li>A person in the grip of a demon can be mistaken for a person who has destroyed his own delusions.</li>
      <li>A charlatan can be mistaken for a siddha.</li>
      <li>An act to benefit yourself can be mistaken for an act to benefit others.</li>
      <li>Deviousness can be mistaken for skilful means.</li>
    </ol>

    <footer class="dedication-band">
      <p class="dedication-bo" lang="bo">འགྲོ་ཀུན་ལྷན་ཅིག་སངས་རྒྱས་ཐོབ་པར་ཤོག</p>
      <p class="dedication-zh" lang="zh">愿一切有情共证佛果位。</p>
      <p class="dedication-en">May all attain Buddhahood together.</p>
      <div class="lotus-placeholder" role="img" aria-label="Outlined lotus flower emblem"></div>
    </footer>
  </main>
</body>
</html>
```